Storefront signage for Physio clinic

We need a design for our storefront windows at our physiotherapy & Pilates clinic.

The design should be modern and include our logo, website url and services (physiotherapy, pilates, massage).

Some inspirational exercise/pilates/recovery quotes may be included and I would like to see the use of sport/pilates/injury related stock images. I have attached a few examples of what we want (images numbered 1-5). And I have attached our current design and photo of the outside of our clinic.

In the attached images there is also a pdf with measurments of our window panels. We require signage for the areas marked 1-10. As you can see on our current signage, you don't need to have a separate image for each panel, these can flow onto each other.
Updates

Industry/Entity Type

Clinic

Colors
85acd3
3377b5
3277b5
e8e8e8
c3c3c3
9d9d9d
848484
7f7f7f

Requirements
Must have
• Stock images related to sports, physiotherapy and pilates
• Ideally these images should be in greyscale and blend in with the rest of the panel which should include colours.
• I would like to see for example a runner, a weightlifter, someone doing pilates, someone with back pain (not necessarily all of these).
Should not have
• I want a creative, modern, up market design, not just a standard recycled template.

```html
<!DOCTYPE html>
<html lang="en">
<head>
<meta charset="UTF-8">
<title>Harbourline Physio &amp; Fitness – Window Signage</title>
<link rel="stylesheet" href="https://fonts.googleapis.com/css2?family=Montserrat:wght@500;700;800&family=Open+Sans:wght@400;600;700&display=swap">
<style>
  :root {
    --sky: #85acd3;
    --blue: #3277b5;
    --blue-deep: #225d9c;
    --navy: #1a4682;
    --navy-dark: #143a6e;
    --mist: #e8e8e8;
    --silver: #c3c3c3;
    --grey: #9d9d9d;
    --slate: #848484;
    --charcoal: #2e2e2e;
    --white: #ffffff;
    --backdrop: #f1f2f4;
  }
  * { box-sizing: border-box; margin: 0; padding: 0; }
  html, body { width: 1200px; height: 591px; overflow: hidden; }
  body {
    background: var(--backdrop);
    font-family: "Open Sans", Arial, sans-serif;
    position: relative;
  }

  /* Large window graphics */
  .window-panel {
    position: absolute;
    top: 152px;
    width: 360px;
    height: 284px;
    border-top: 4px solid var(--blue);
    overflow: hidden;
    background: var(--mist);
  }
  .window-panel--fit { left: 21px; }
  .window-panel--sweat { left: 405px; }

  .panel-photo {
    position: absolute;
    inset: 0 0 38px 0;
  }
  .window-panel--fit .panel-photo {
    background:
      radial-gradient(ellipse 70px 60px at 255px 60px, rgba(255,255,255,0.95), rgba(255,255,255,0) 100%),
      radial-gradient(ellipse 120px 40px at 150px 190px, rgba(40,40,40,0.75), rgba(40,40,40,0) 100%),
      radial-gradient(ellipse 60px 80px at 300px 150px, rgba(30,30,30,0.6), rgba(30,30,30,0) 100%),
      radial-gradient(ellipse 140px 50px at 200px 30px, rgba(250,250,250,0.8), rgba(250,250,250,0) 100%),
      linear-gradient(90deg, #3a3a3a 0%, #8a8a8a 18%, #cfcfcf 45%, #d8d8d8 70%, #7a7a7a 100%);
  }
  .window-panel--sweat .panel-photo {
    background:
      radial-gradient(ellipse 90px 70px at 60px 50px, rgba(20,20,20,0.85), rgba(20,20,20,0) 100%),
      radial-gradient(ellipse 80px 60px at 60px 200px, rgba(25,25,25,0.8), rgba(25,25,25,0) 100%),
      radial-gradient(ellipse 100px 70px at 250px 150px, rgba(245,245,245,0.9), rgba(245,245,245,0) 100%),
      radial-gradient(ellipse 70px 50px at 300px 60px, rgba(60,60,60,0.7), rgba(60,60,60,0) 100%),
      linear-gradient(120deg, #2a2a2a 0%, #6a6a6a 30%, #b8b8b8 60%, #8f8f8f 100%);
  }

  .brand-tag {
    position: absolute;
    top: 14px;
    right: 14px;
    display: flex;
    align-items: center;
    gap: 5px;
    color: var(--blue);
    font-family: "Montserrat", Arial, sans-serif;
    font-weight: 800;
    font-size: 10px;
    line-height: 1;
  }
  .brand-tag__dot {
    width: 14px; height: 14px;
    border-radius: 50%;
    background: var(--blue);
  }
  .brand-tag__sub {
    display: block;
    font-family: "Montserrat", Arial, sans-serif;
    font-weight: 800;
    font-size: 5px;
    color: var(--blue);
    margin-top: 2px;
  }

  .headline {
    position: absolute;
    left: 18px;
    font-family: "Montserrat", Arial, sans-serif;
    font-weight: 800;
    color: var(--white);
    text-transform: uppercase;
    line-height: 0.98;
    letter-spacing: 0.5px;
    text-shadow: 0 1px 3px rgba(0,0,0,0.35);
  }
  .window-panel--fit .headline { top: 46px; font-size: 30px; }
  .window-panel--sweat .headline { top: 66px; font-size: 30px; }
  .headline__tagline {
    display: block;
    font-family: "Open Sans", Arial, sans-serif;
    font-weight: 600;
    font-size: 9px;
    text-transform: none;
    letter-spacing: 0;
    margin-top: 4px;
  }

  .enrol-box {
    position: absolute;
    left: 18px;
    width: 86px;
    background: var(--navy-dark);
    color: var(--white);
    text-align: center;
    padding: 3px 4px 4px;
  }
  .window-panel--fit .enrol-box { top: 152px; }
  .window-panel--sweat .enrol-box { top: 156px; }
  .enrol-box__label { display: block; font-size: 5px; font-weight: 700; letter-spacing: 0.5px; }
  .enrol-box__phone { display: block; font-family: "Montserrat", Arial, sans-serif; font-size: 9px; font-weight: 700; }

  .web-line {
    position: absolute;
    right: 14px;
    bottom: 44px;
    font-size: 6px;
    color: var(--white);
  }

  .service-bar {
    position: absolute;
    left: 0; right: 0; bottom: 0;
    height: 38px;
    display: grid;
    grid-template-columns: repeat(4, 1fr);
    list-style: none;
  }
  .service-bar__item {
    position: relative;
    color: var(--white);
    font-size: 6.5px;
    font-weight: 700;
    text-transform: uppercase;
    letter-spacing: 0.4px;
    padding: 6px 8px;
  }
  .service-bar__item::after {
    content: "";
    position: absolute;
    right: 5px;
    bottom: 5px;
    width: 3px;
    height: 3px;
    background: var(--white);
  }
  .service-bar__item:nth-child(1) { background: var(--sky); }
  .service-bar__item:nth-child(2) { background: var(--blue); }
  .service-bar__item:nth-child(3) { background: var(--blue-deep); }
  .service-bar__item:nth-child(4) { background: var(--navy); }

  /* Door-side panels */
  .door-panel {
    position: absolute;
    top: 146px;
    width: 120px;
    height: 300px;
    color: var(--white);
  }
  .door-panel--left {
    left: 789px;
    background: linear-gradient(to bottom, var(--navy) 0 54%, var(--navy-dark) 54% 100%);
  }
  .door-panel--right {
    left: 1059px;
    background: linear-gradient(to bottom, #4a88c6 0 46%, var(--blue) 46% 100%);
  }
  .door-panel__photo {
    position: absolute;
    top: 92px;
    left: 22px;
    width: 76px;
    height: 98px;
    border: 3px solid var(--white);
  }
  .door-panel--left .door-panel__photo {
    background:
      radial-gradient(ellipse 30px 40px at 25px 30px, rgba(70,70,70,0.8), rgba(70,70,70,0) 100%),
      radial-gradient(ellipse 30px 30px at 50px 70px, rgba(240,240,240,0.9), rgba(240,240,240,0) 100%),
      linear-gradient(150deg, #bdbdbd, #8a8a8a 55%, #4e4e4e);
  }
  .door-panel--right .door-panel__photo {
    top: 98px;
    background:
      radial-gradient(ellipse 35px 20px at 35px 70px, rgba(40,40,40,0.75), rgba(40,40,40,0) 100%),
      radial-gradient(ellipse 30px 30px at 50px 20px, rgba(245,245,245,0.9), rgba(245,245,245,0) 100%),
      linear-gradient(160deg, #d0d0d0, #8a8a8a 55%, #c8c8c8);
  }

  .door-panel__phone {
    position: absolute;
    bottom: 24px;
    left: 0; right: 0;
    display: flex;
    align-items: center;
    justify-content: center;
    gap: 4px;
    font-family: "Montserrat", Arial, sans-serif;
    font-size: 8px;
    font-weight: 700;
  }
  .door-panel__details {
    position: absolute;
    bottom: 14px;
    left: 12px; right: 8px;
    font-size: 5.5px;
    line-height: 1.45;
  }

  /* Door decal */
  .door-decal {
    position: absolute;
    left: 928px;
    top: 245px;
    width: 112px;
    height: 112px;
    border: 2px solid var(--sky);
    border-radius: 50%;
    display: flex;
    flex-direction: column;
    align-items: center;
    justify-content: center;
    text-align: center;
    color: var(--blue);
    font-family: "Montserrat", Arial, sans-serif;
    font-weight: 800;
    font-size: 11px;
    line-height: 1.1;
  }
  .door-decal__dot {
    width: 14px; height: 14px;
    border-radius: 50%;
    background: var(--blue);
    margin-bottom: 5px;
  }
</style>
</head>
<body>

  <section class="window-panel window-panel--fit">
    <div class="panel-photo" role="img" aria-label="Greyscale photo of a trainer guiding a woman through a push-up in a gym"></div>
    <div class="brand-tag">
      <span class="brand-tag__dot"></span>
      <span>HARBOURLINE<span class="brand-tag__sub">Physio &amp; Fitness</span></span>
    </div>
    <h2 class="headline">Turn<br>fat to<br>fit</h2>
    <div class="enrol-box">
      <span class="enrol-box__label">ENROL NOW!</span>
      <span class="enrol-box__phone">02 5550 1834</span>
    </div>
    <span class="web-line">www.harbourlinephysio.com.au</span>
    <ul class="service-bar">
      <li class="service-bar__item">Physiotherapy</li>
      <li class="service-bar__item">Pilates</li>
      <li class="service-bar__item">Massage</li>
      <li class="service-bar__item">Work Rehabilitation</li>
    </ul>
  </section>

  <section class="window-panel window-panel--sweat">
    <div class="panel-photo" role="img" aria-label="Greyscale photo of a woman lifting a dumbbell beside a weights rack"></div>
    <div class="brand-tag">
      <span class="brand-tag__dot"></span>
      <span>HARBOURLINE<span class="brand-tag__sub">Physio &amp; Fitness</span></span>
    </div>
    <h2 class="headline">Good<br>things<span class="headline__tagline">come to those who sweat</span></h2>
    <div class="enrol-box">
      <span class="enrol-box__label">ENROL NOW!</span>
      <span class="enrol-box__phone">02 5550 1834</span>
    </div>
    <ul class="service-bar">
      <li class="service-bar__item">Physiotherapy</li>
      <li class="service-bar__item">Pilates</li>
      <li class="service-bar__item">Massage</li>
      <li class="service-bar__item">Work Rehabilitation</li>
    </ul>
  </section>

  <aside class="door-panel door-panel--left">
    <div class="door-panel__photo" role="img" aria-label="Greyscale photo of a physiotherapist treating a patient's leg"></div>
    <p class="door-panel__phone">
      <svg width="8" height="8" viewBox="0 0 24 24" aria-hidden="true"><path fill="#ffffff" d="M6.6 10.8a15.1 15.1 0 0 0 6.6 6.6l2.2-2.2a1 1 0 0 1 1-.25 11.4 11.4 0 0 0 3.6.57 1 1 0 0 1 1 1V20a1 1 0 0 1-1 1A17 17 0 0 1 3 4a1 1 0 0 1 1-1h3.5a1 1 0 0 1 1 1c0 1.25.2 2.45.57 3.6a1 1 0 0 1-.25 1z"/></svg>
      02 5550 1834
    </p>
  </aside>

  <div class="door-decal">
    <span class="door-decal__dot"></span>
    HARBOURLINE
  </div>

  <aside class="door-panel door-panel--right">
    <div class="door-panel__photo" role="img" aria-label="Greyscale photo of a woman doing a Pilates exercise on a mat"></div>
    <p class="door-panel__details">
      Shop 3, 12 Marlow St<br>
      Harbourline<br>
      www.harbourlinephysio.com.au
    </p>
  </aside>

</body>
</html>
```